We are a recruitment company based in Norwich/Cambridge England.
I have included our company logo which we want to remain the same.

What we are looking for is a new creative Business card which will really stand out!!

Contact Information for Business Card

Harriet Dunmore
email: Harriet@plavex.co.uk
Address: Brackwell House
Fenmoor Enterprise Park
Partridge Way
Norwich
QB9 3KX
Tel:01632 960418

```html
<!DOCTYPE html>
<html lang="en">
<head>
<meta charset="utf-8">
<title>Plavex Business Card</title>
<link rel="stylesheet" href="https://fonts.googleapis.com/css2?family=Open+Sans:wght@400;600;700&display=swap">
<style>
  :root {
    --stage: #e9e7e3;
    --card-white: #f7f7f6;
    --grey: #a3a2a7;
    --grey-dark: #8e8d93;
    --grey-light: #b4b3b8;
    --green: #8cc63f;
    --green-light: #a6d45a;
    --ink-grey: #7d7c82;
    --white: #ffffff;
  }
  * { box-sizing: border-box; margin: 0; padding: 0; }
  html, body { width: 1200px; height: 780px; overflow: hidden; }
  body {
    background: var(--stage);
    font-family: "Open Sans", Arial, sans-serif;
    display: flex;
    align-items: center;
    justify-content: center;
    gap: 40px;
  }
  .card {
    position: relative;
    width: 540px;
    height: 310px;
    overflow: hidden;
    box-shadow: 0 6px 18px rgba(0,0,0,0.18);
  }

  /* Front */
  .card-front { background: var(--card-white); }
  .front-brand {
    position: absolute;
    left: 40px;
    top: 78px;
    display: flex;
    align-items: center;
    gap: 14px;
  }
  .brand-dot {
    width: 46px; height: 46px;
    border-radius: 50%;
    background: var(--green);
  }
  .brand-text { display: flex; flex-direction: column; }
  .brand-name {
    font-weight: 700;
    font-size: 46px;
    line-height: 1;
    color: var(--green);
    letter-spacing: -1px;
  }
  .brand-tagline {
    font-size: 10px;
    letter-spacing: 3px;
    color: var(--ink-grey);
    margin-top: 4px;
  }
  .front-contact {
    position: absolute;
    left: 0; right: 0; bottom: 0;
    height: 132px;
    background: var(--grey);
  }
  .name-bar {
    position: absolute;
    left: 0; top: 0;
    width: 300px;
    height: 32px;
    background: var(--green);
    display: flex;
    align-items: center;
    padding-left: 36px;
    color: var(--white);
  }
  .name-bar::after {
    content: "";
    position: absolute;
    left: 300px; top: 0;
    width: 240px; height: 4px;
    background: var(--green);
  }
  .person-name { font-weight: 700; font-size: 17px; }
  .divider { margin: 0 10px; opacity: .8; font-weight: 400; }
  .person-role { font-size: 14px; }
  .side-strip {
    position: absolute;
    left: 0; top: 32px; bottom: 0;
    width: 16px;
    background: var(--green);
  }
  .contact-list {
    position: absolute;
    left: 36px; top: 42px;
    list-style: none;
    color: var(--white);
    font-size: 12px;
    line-height: 17px;
  }
  .contact-list li { display: flex; align-items: center; gap: 8px; }
  .contact-list .plain { padding-left: 24px; }
  .icon {
    width: 16px; height: 16px;
    flex: none;
  }

  /* Back */
  .card-back {
    background: radial-gradient(circle at 58% 45%, var(--grey-light) 0%, var(--grey) 55%, var(--grey-dark) 100%);
  }
  .back-strip {
    position: absolute;
    left: 0; top: 0; bottom: 0;
    width: 44px;
    background: var(--green);
    display: flex;
    align-items: center;
    justify-content: center;
  }
  .back-web {
    writing-mode: vertical-rl;
    color: var(--white);
    font-size: 13px;
    letter-spacing: 2px;
  }
  .back-brand {
    position: absolute;
    left: 44px; right: 0; top: 0; bottom: 0;
    display: flex;
    align-items: center;
    justify-content: center;
    gap: 16px;
  }
  .back-brand .brand-dot { background: var(--white); width: 54px; height: 54px; }
  .back-brand .brand-name { color: var(--white); font-size: 58px; }
  .back-brand .brand-tagline { color: var(--white); }
</style>
</head>
<body>

  <section class="card card-front" aria-label="Business card front">
    <div class="front-brand">
      <span class="brand-dot"></span>
      <div class="brand-text">
        <span class="brand-name">Plavex</span>
        <span class="brand-tagline">Technology Recruitment</span>
      </div>
    </div>

    <div class="front-contact">
      <div class="name-bar">
        <span class="person-name">Harriet Dunmore</span>
        <span class="divider">|</span>
        <span class="person-role">CEO</span>
      </div>
      <div class="side-strip"></div>
      <ul class="contact-list">
        <li class="plain">Brackwell House, Fenmoor Enterprise Park</li>
        <li class="plain">Partridge Way, Norwich QB9 3KX</li>
        <li>
          <svg class="icon" viewBox="0 0 16 16" aria-hidden="true"><circle cx="8" cy="8" r="7.3" fill="none" stroke="#fff" stroke-width="1"/><rect x="5.5" y="4" width="5" height="8" rx="1" fill="none" stroke="#fff" stroke-width="1"/></svg>
          01632 960418
        </li>
        <li>
          <svg class="icon" viewBox="0 0 16 16" aria-hidden="true"><circle cx="8" cy="8" r="7.3" fill="none" stroke="#fff" stroke-width="1"/><rect x="4" y="5" width="8" height="6" fill="none" stroke="#fff" stroke-width="1"/><path d="M4 5l4 3.5L12 5" fill="none" stroke="#fff" stroke-width="1"/></svg>
          Harriet@plavex.co.uk
        </li>
        <li>
          <svg class="icon" viewBox="0 0 16 16" aria-hidden="true"><circle cx="8" cy="8" r="7.3" fill="none" stroke="#fff" stroke-width="1"/><circle cx="8" cy="8" r="4" fill="none" stroke="#fff" stroke-width="1"/><path d="M4 8h8M8 4v8" stroke="#fff" stroke-width="1"/></svg>
          www.plavex.co.uk
        </li>
      </ul>
    </div>
  </section>

  <section class="card card-back" aria-label="Business card back">
    <div class="back-strip">
      <span class="back-web">www.plavex.co.uk</span>
    </div>
    <div class="back-brand">
      <span class="brand-dot"></span>
      <div class="brand-text">
        <span class="brand-name">Plavex</span>
        <span class="brand-tagline">Technology Recruitment</span>
      </div>
    </div>
  </section>

</body>
</html>
```